Business Card Design Project

I need a business card design for an Organic drive thru coffee kiosk. We will serve organic coffee, teas & smoothies and will serve healthy breakfast food/snacks for people on the go.
I want the card to have 2-3 colors max (earthy colors like browns, greens and so on).
I have attached the logo I want used and would love to play off the theme of "balance."
Include:
Sun-Leaf Coffee
address: 3712 Pelwin Ct. Raleigh, NC 27699
phone: 919-555-0143
website: www.sun-leaf.com (website is not up yet but still include it on card)
email: Dorothy@sun-leaf.com
I want one of the following sayings somewhere on the card (the front or back is fine):
"Eat & Drink Well, on the run!"
"Break the fast with Sun-Leaf"
Maybe on the back list what we offer:
-Organic coffee, espresso & tea
-Blendora smoothies & protein shakes
-Zippy Tonic (100% fresh local fruit and veggies)
-Vital Nibbles
College age to 55
Business

```html
<!DOCTYPE html>
<html lang="en">
<head>
<meta charset="utf-8">
<title>Sun-Leaf Coffee – Business Cards</title>
<link href="https://fonts.googleapis.com/css2?family=PT+Sans:wght@400;700&display=swap" rel="stylesheet">
<style>
  :root {
    --backdrop: #efece4;
    --bean-brown: #98693f;
    --leaf-green: #5e9540;
    --roast: #4a2e1e;
    --sprout: #b3db77;
    --sprout-soft: #c4e49a;
    --cream: #e8d9a8;
    --glow-on-brown: rgba(226, 170, 110, 0.35);
    --glow-on-green: rgba(170, 210, 140, 0.35);
  }
  * { box-sizing: border-box; margin: 0; padding: 0; }
  html, body { width: 1200px; height: 900px; overflow: hidden; }
  body {
    background: var(--backdrop);
    font-family: "PT Sans", Arial, sans-serif;
    position: relative;
  }
  .card {
    position: absolute;
    overflow: hidden;
    box-shadow: 7px 9px 12px rgba(0, 0, 0, 0.38);
  }
  .card--brown { background: var(--bean-brown); }
  .card--green { background: var(--leaf-green); }

  .card--front-brown { left: 71px; top: 119px; width: 484px; height: 269px; }
  .card--back-green  { left: 621px; top: 117px; width: 478px; height: 265px; }
  .card--front-green { left: 71px; top: 500px; width: 484px; height: 270px; }
  .card--back-brown  { left: 614px; top: 498px; width: 485px; height: 270px; }

  /* faint decorative disc */
  .glow {
    position: absolute;
    border-radius: 50%;
  }
  .card--brown .glow { background: var(--glow-on-brown); }
  .card--green .glow { background: var(--glow-on-green); }
  .card--front-brown .glow,
  .card--front-green .glow { width: 200px; height: 200px; left: 135px; top: 28px; }
  .card--back-green .glow { width: 170px; height: 170px; left: 290px; top: 55px; }
  .card--back-brown .glow { width: 170px; height: 170px; left: 25px; top: 55px; }

  /* name lockup */
  .brand {
    position: absolute;
    display: flex;
    align-items: center;
    gap: 10px;
    color: var(--roast);
    font-weight: 400;
    white-space: nowrap;
  }
  .brand__dot {
    width: 26px; height: 26px;
    border-radius: 50%;
    background: var(--roast);
  }
  .card--front-brown .brand,
  .card--front-green .brand { font-size: 50px; left: 0; right: 0; top: 96px; justify-content: center; }
  .card--back-green .brand { font-size: 40px; left: 12px; width: 238px; top: 100px; justify-content: center; }
  .card--back-brown .brand { font-size: 40px; left: 250px; width: 235px; top: 100px; justify-content: center; }

  /* front */
  .site {
    position: absolute;
    left: 14px; top: 8px;
    font-size: 13px;
    color: var(--sprout);
  }
  .offers {
    position: absolute;
    left: 10px; right: 14px; bottom: 10px;
    display: flex;
    justify-content: space-between;
    font-size: 13px;
    line-height: 1.3;
    color: var(--sprout);
  }
  .offers__col--right { text-align: right; }

  /* back */
  .divider {
    position: absolute;
    top: 22px;
    width: 1px;
    height: 200px;
  }
  .card--back-green .divider { left: 254px; background: var(--bean-brown); }
  .card--back-brown .divider { left: 245px; background: var(--leaf-green); }

  .contact {
    position: absolute;
    top: 28px;
    font-size: 12px;
    line-height: 1.3;
  }
  .contact__company {
    font-size: 18px;
    color: var(--roast);
    margin-bottom: 4px;
  }
  .contact__person {
    font-size: 13px;
    color: var(--roast);
    margin-top: 62px;
  }
  .card--back-green .contact { right: 34px; text-align: right; color: var(--sprout); }
  .card--back-brown .contact { left: 25px; text-align: left; color: var(--sprout); }

  .band {
    position: absolute;
    left: 0; right: 0; bottom: 0;
    height: 32px;
    display: flex;
    align-items: center;
    justify-content: center;
    gap: 28px;
    font-size: 15px;
    white-space: nowrap;
  }
  .card--back-green .band { background: var(--bean-brown); color: var(--cream); }
  .card--back-brown .band { background: var(--leaf-green); color: var(--cream); height: 28px; }
</style>
</head>
<body>

  <section class="card card--brown card--front-brown">
    <div class="glow" role="img" aria-label="Faint decorative disc behind the name"></div>
    <p class="site">www.sun-leaf.com</p>
    <div class="brand"><span class="brand__dot"></span>Sun-Leaf</div>
    <div class="offers">
      <div class="offers__col">Organic Coffee, espresso &amp; tea<br>Zippy Tonic (100% local fruit &amp; veggies)</div>
      <div class="offers__col offers__col--right">Blendora smoothies &amp; protein shakes<br>Vital Nibbles</div>
    </div>
  </section>

  <section class="card card--green card--back-green">
    <div class="glow" role="img" aria-label="Faint decorative disc behind contact details"></div>
    <div class="brand"><span class="brand__dot"></span>Sun-Leaf</div>
    <div class="divider"></div>
    <div class="contact">
      <p class="contact__company">Sun-Leaf Coffee</p>
      <p>3712 Pelwin Ct. Raleigh, NC 27699</p>
      <p class="contact__person">Dorothy</p>
      <p>919-555-0143</p>
      <p>Dorothy@sun-leaf.com</p>
    </div>
    <div class="band"><span>Eat and drink well, on the run !.</span><span>Break the fast, with Sun-Leaf</span></div>
  </section>

  <section class="card card--green card--front-green">
    <div class="glow" role="img" aria-label="Faint decorative disc behind the name"></div>
    <p class="site">www.sun-leaf.com</p>
    <div class="brand"><span class="brand__dot"></span>Sun-Leaf</div>
    <div class="offers">
      <div class="offers__col">Organic Coffee, espresso &amp; tea<br>Zippy Tonic (100% local fruit &amp; veggies)</div>
      <div class="offers__col offers__col--right">Blendora smoothies &amp; protein shakes<br>Vital Nibbles</div>
    </div>
  </section>

  <section class="card card--brown card--back-brown">
    <div class="glow" role="img" aria-label="Faint decorative disc behind contact details"></div>
    <div class="contact">
      <p class="contact__company">Sun-Leaf Coffee</p>
      <p>3712 Pelwin Ct. Raleigh, NC 27699</p>
      <p class="contact__person">Dorothy</p>
      <p>919-555-0143</p>
      <p>Dorothy@sun-leaf.com</p>
    </div>
    <div class="divider"></div>
    <div class="brand"><span class="brand__dot"></span>Sun-Leaf</div>
    <div class="band"><span>Eat and drink well, on the run !.</span><span>Break the fast, with Sun-Leaf</span></div>
  </section>

</body>
</html>
```